Request for Business Card Design

Hi. My name is Marlene, I am looking for a new business card design for my company, Quarrow Signal Instruments, LLC. I really like the design you did for Tarsel Venture and was hoping you could do something similar using our full logo and our mark. I am also open to any raised texture design using our mark. I have attached our full logo, which would need to be somewhere on the card, as well as the mark in both outline and full form, as well as our brand colors / guide. The card does not have to be white, as long as our logo and mark appear. I actually like darker colored business cards more, but am open to all options. If you are interested in working with me, please let me know. We would also take the business card design into letterhead design if you can do that.

```html
<!DOCTYPE html>
<html lang="en">
<head>
<meta charset="utf-8">
<title>Quarrow Signal Instruments — Business Card</title>
<link rel="stylesheet" href="https://fonts.googleapis.com/css2?family=Barlow:wght@500;600&family=Roboto:wght@400;500&display=swap">
<style>
  :root {
    --backdrop: #b3b3b3;
    --card: #1f1f1f;
    --brand-blue: #0a9bc6;
    --ink-white: #ffffff;
    --ink-soft: #c9c9c9;
  }
  html, body {
    margin: 0;
    width: 1093px;
    height: 1200px;
    overflow: hidden;
    background: var(--backdrop);
  }
  .sheet { position: relative; width: 1093px; height: 1200px; }
  .card {
    position: absolute;
    background: var(--card);
    box-shadow: 2px 3px 3px rgba(0,0,0,.45);
  }
  .card--front {
    left: 264px; top: 226px; width: 579px; height: 357px;
    border-top-right-radius: 135px 130px;
  }
  .card--back {
    left: 264px; top: 620px; width: 582px; height: 357px;
    border-top-left-radius: 134px 101px;
  }
  .wordmark {
    position: absolute;
    font-family: "Barlow", sans-serif;
    color: var(--ink-white);
    line-height: 1;
  }
  .wordmark__name {
    display: block;
    font-weight: 600;
    letter-spacing: 4px;
  }
  .wordmark__tagline {
    display: block;
    font-weight: 500;
    letter-spacing: 1.4px;
  }
  .card--front .wordmark { left: 27px; top: 48px; }
  .card--front .wordmark__name { font-size: 46px; }
  .card--front .wordmark__tagline { font-size: 15px; margin-top: 1px; }
  .card--back .wordmark { left: 229px; top: 142px; }
  .card--back .wordmark__name { font-size: 50px; }
  .card--back .wordmark__tagline { font-size: 18px; margin-top: 3px; letter-spacing: 1.8px; }

  .brand-dot {
    position: absolute; left: 110px; top: 142px;
    width: 73px; height: 73px; border-radius: 50%;
    background: var(--brand-blue);
  }

  .person { position: absolute; left: 27px; top: 160px; font-family: "Roboto", sans-serif; }
  .person__name { margin: 0; font-size: 26px; font-weight: 500; color: var(--brand-blue); line-height: 1; }
  .person__role { margin: 1px 0 0; font-size: 17px; color: var(--ink-soft); line-height: 1.1; }

  .contact {
    position: absolute; left: 27px; top: 217px;
    list-style: none; margin: 0; padding: 0;
    font-family: "Roboto", sans-serif; font-size: 17px; color: var(--ink-soft);
  }
  .contact li { display: flex; align-items: center; height: 21px; }
  .contact svg { width: 15px; height: 15px; margin-right: 8px; fill: none; stroke: var(--brand-blue); stroke-width: 2; }
  .contact .icon-fill { fill: var(--brand-blue); stroke: none; }

  .address {
    position: absolute; left: 27px; top: 290px; margin: 0;
    font-family: "Roboto", sans-serif; font-style: normal;
    font-size: 17px; line-height: 21px; color: var(--ink-soft);
  }
</style>
</head>
<body>
<main class="sheet">
  <section class="card card--front" aria-label="Card front">
    <div class="wordmark">
      <span class="wordmark__name">QUARROW</span>
      <span class="wordmark__tagline">SIGNAL INSTRUMENTS</span>
    </div>
    <div class="person">
      <h1 class="person__name">MARLENE AVERY</h1>
      <p class="person__role">Managing Director</p>
    </div>
    <ul class="contact">
      <li>
        <svg viewBox="0 0 16 16" aria-hidden="true"><path class="icon-fill" d="M3 1.5l2.5-.5 1.5 3.5-1.8 1.2a9 9 0 0 0 5 5l1.2-1.8 3.5 1.5-.5 2.5c-.4.8-1.2 1-2 1A12 12 0 0 1 1 3.5c0-.8.2-1.6 2-2z"/><path d="M10 1.5a5 5 0 0 1 4.5 4.5M9.5 4a2.5 2.5 0 0 1 2.5 2.5"/></svg>
        021-555 018 204
      </li>
      <li>
        <svg viewBox="0 0 16 16" aria-hidden="true"><rect class="icon-fill" x="0" y="3" width="16" height="11"/><path d="M0.5 3.5l7.5 6 7.5-6" stroke="#1f1f1f" stroke-width="1.3"/></svg>
        hello@quarrowsignal.com
      </li>
      <li>
        <svg viewBox="0 0 16 16" aria-hidden="true"><circle cx="8" cy="8" r="7" stroke-width="1.4"/><ellipse cx="8" cy="8" rx="3" ry="7" stroke-width="1.2"/><path d="M1 8h14M2.5 4.5h11M2.5 11.5h11" stroke-width="1.2"/></svg>
        www.quarrowsignal.com
      </li>
    </ul>
    <address class="address">18, Harlow Street, Suite 40<br>60418,Eastmere Bay</address>
  </section>

  <section class="card card--back" aria-label="Card back">
    <span class="brand-dot" aria-hidden="true"></span>
    <div class="wordmark">
      <span class="wordmark__name">QUARROW</span>
      <span class="wordmark__tagline">SIGNAL INSTRUMENTS</span>
    </div>
  </section>
</main>
</body>
</html>
```